Stationery Design Project

I need a stationary design for our company. we are based in Brookvale, OK and we are called Mira Vell Lending. And we are wanting to brand our MoneyMendPlus program, which includes our tax preparation and restoration, credit repair service. Although our business offers other programs, we are interested in mainly focusing on The MoneyMendPlus program. We are looking for way to brand our ourselves and I believe that a great stationery design will help in achieving this goal. Our logo design is blue and light blue. the slogan is orange.

Industry/Entity Type

Business

Requirements
Must have
• Address: 30871 Calloway Ln. B-22
Brookvale, OK 75419
Tel. 555-318-6207
Fax 555-294-7153
www.miravelllending.example
info@miravelllending.example
Our Slogan: Confidence, Renewed!

```html
<!DOCTYPE html>
<html lang="en">
<head>
<meta charset="utf-8">
<title>MoneyMendPlus Business Cards</title>
<link rel="stylesheet" href="https://fonts.googleapis.com/css2?family=Jost:wght@400;500&family=Tinos:wght@400;700&display=swap">
<style>
  :root {
    --backdrop: #ecebe8;
    --card: #ffffff;
    --navy: #123e6b;
    --blue: #1f6fae;
    --orange: #f39a1e;
    --ink: #2b2b2b;
    --rule: #c9ccd1;
  }
  * { box-sizing: border-box; margin: 0; padding: 0; }
  html, body { width: 1200px; height: 729px; overflow: hidden; }
  body { background: var(--backdrop); font-family: "Jost", sans-serif; position: relative; }

  .card {
    position: absolute;
    width: 540px;
    height: 309px;
    background: var(--card);
    box-shadow: 0 2px 10px rgba(0,0,0,.12);
  }
  .card--front { left: 40px; top: 150px; }
  .card--back { left: 620px; top: 270px; }

  .program-name {
    font-family: "Jost", sans-serif;
    font-weight: 500;
    color: var(--blue);
    letter-spacing: -0.5px;
    display: flex;
    align-items: center;
    gap: 12px;
  }
  .program-name__dot {
    width: 18px; height: 18px; border-radius: 50%;
    background: var(--navy);
    flex: none;
  }
  .card--front .program-name {
    position: absolute; left: 0; right: 0; top: 58px;
    justify-content: center; font-size: 46px;
  }
  .program-rule {
    position: absolute; height: 4px; background: var(--navy);
  }
  .card--front .program-rule { left: 110px; width: 330px; top: 50px; }

  .lender {
    position: absolute; left: 36px; top: 160px;
    width: 150px; display: flex; flex-direction: column; align-items: center; gap: 10px;
  }
  .lender__mark { width: 70px; height: 70px; background: var(--navy); border: 3px solid #b7c6d8; }
  .lender__name { font-family: "Jost", sans-serif; font-weight: 500; color: var(--navy); font-size: 15px; text-align: center; }

  .divider {
    position: absolute; left: 208px; top: 150px; width: 1px; height: 130px;
    background: var(--rule);
  }
  .contact {
    position: absolute; left: 226px; top: 150px;
    color: var(--ink); font-size: 15px; line-height: 1.3;
  }
  .contact__address { margin-bottom: 12px; }
  .contact__list { list-style: none; }
  .contact__item { display: flex; align-items: center; gap: 8px; margin-bottom: 3px; }
  .contact__icon { width: 12px; height: 12px; flex: none; }

  .card--back .program-name {
    position: absolute; left: 0; right: 0; top: 96px;
    justify-content: center; font-size: 56px;
  }
  .card--back .program-rule { left: 70px; width: 400px; top: 86px; }
  .slogan {
    position: absolute; left: 0; right: 0; top: 186px; text-align: center;
    font-family: "Tinos", serif; font-weight: 700; color: var(--orange);
    font-size: 22px; letter-spacing: 6px; text-transform: uppercase;
  }
  .back-web {
    position: absolute; left: 0; right: 0; top: 240px; text-align: center;
    font-family: "Tinos", serif; color: var(--navy); font-size: 14px; letter-spacing: 3px;
  }
  .back-web strong { font-weight: 700; }
</style>
</head>
<body>

<section class="card card--front" aria-label="Business card front">
  <div class="program-rule"></div>
  <div class="program-name"><span class="program-name__dot"></span>MoneyMendPlus</div>

  <div class="lender">
    <div class="lender__mark"></div>
    <div class="lender__name">Mira Vell Lending</div>
  </div>

  <div class="divider"></div>

  <div class="contact">
    <p class="contact__address">30871 Calloway Ln. B-22<br>Brookvale, OK 75419</p>
    <ul class="contact__list">
      <li class="contact__item">
        <svg class="contact__icon" viewBox="0 0 12 12"><path d="M2 1l2 0 1 3-1.5 1a6 6 0 0 0 3 3L7.5 6.5l3 1v2a1.5 1.5 0 0 1-1.5 1.5A9 9 0 0 1 .5 2.5 1.5 1.5 0 0 1 2 1z" fill="var(--navy)"/></svg>
        555-318-6207
      </li>
      <li class="contact__item">
        <svg class="contact__icon" viewBox="0 0 12 12"><rect x="3" y="1" width="6" height="3" fill="var(--navy)"/><rect x="1" y="4.5" width="10" height="5" rx="1" fill="var(--navy)"/><rect x="3" y="8" width="6" height="3" fill="#fff" stroke="var(--navy)"/></svg>
        555-294-7153
      </li>
      <li class="contact__item">
        <svg class="contact__icon" viewBox="0 0 12 12"><rect x="1" y="2.5" width="10" height="7" rx="1" fill="var(--navy)"/><path d="M1.5 3l4.5 3.5L10.5 3" stroke="#fff" fill="none"/></svg>
        info@miravelllending.example
      </li>
      <li class="contact__item">
        <svg class="contact__icon" viewBox="0 0 12 12" fill="none" stroke="var(--navy)"><circle cx="6" cy="6" r="5"/><ellipse cx="6" cy="6" rx="2.2" ry="5"/><path d="M1 6h10"/></svg>
        www.miravelllending.example
      </li>
    </ul>
  </div>
</section>

<section class="card card--back" aria-label="Business card back">
  <div class="program-rule"></div>
  <div class="program-name"><span class="program-name__dot"></span>MoneyMendPlus</div>
  <p class="slogan">Confidence, Renewed!</p>
  <p class="back-web">www.<strong>miravelllending</strong>.example</p>
</section>

</body>
</html>
```